Hartwell Estates Business Cards

I would like a business card that includes myself and my partner.
Includes: Logo, office #, email, website, our names, our numbers and possibly the address. I would also like the logo to be embossed and the card to be horizontal.
There is a photo of our yard signs to give you an idea of the colors of our business.

Target Market(s)

Everyone in real estate market.
We are in a rural area. Our clientele are from all socioeconomic backgrounds.

Industry/Entity Type

Real Estate Agent

Contact Information for Business Card

Company Name: Hartwell Estates
Our Names, Titles & Cell #'s : Dana Pembrook-Broker (555).317.6624, Marla Pembrook-Realtor (555).609.1385
Office #: (555).240.3918
Website: hartwellestates-demo.com
Joint Email: pembrook@hartwellestates-demo.com
Office Address: 418B W. Calloway Ave.
Linden Falls, OK. 70913

Font styles to use
Serif

Requirements
Must have
• HORIZONTAL, Logo, Myself and my partners names, Our cell #'s, our office #, our website, our email address
Nice to have
• Embossed logo, office address, our titles.

```html
<!DOCTYPE html>
<html lang="en">
<head>
<meta charset="utf-8">
<title>Hartwell Estates Business Cards</title>
<link rel="stylesheet" href="https://fonts.googleapis.com/css2?family=Montserrat:wght@400;500;600;700&display=swap">
<style>
  :root {
    --bg: #2b2b2d;
    --purple: #4b0f6b;
    --purple-emboss: #5c2a86;
    --purple-text: #4b1670;
    --grey-title: #6e6e6e;
    --olive: #3e3e24;
    --white: #ffffff;
  }
  * { margin: 0; padding: 0; box-sizing: border-box; }
  html, body { width: 1200px; height: 900px; overflow: hidden; }
  body {
    background: var(--bg);
    font-family: "Montserrat", sans-serif;
    position: relative;
  }
  .card {
    position: absolute;
    width: 620px;
    height: 354px;
    border-radius: 26px;
    overflow: hidden;
  }
  /* Back side */
  .card-back {
    left: 110px; top: 80px;
    background: var(--purple);
  }
  .brand-emboss {
    position: absolute;
    left: 0; right: 0; top: 120px;
    text-align: center;
    color: var(--purple-emboss);
    font-size: 46px;
    font-weight: 700;
    letter-spacing: 1px;
  }
  .brand-emboss .mark {
    display: inline-block;
    width: 36px; height: 36px;
    border-radius: 50%;
    background: var(--purple-emboss);
    vertical-align: middle;
    margin-right: 16px;
    position: relative; top: -4px;
  }
  .back-web {
    position: absolute;
    right: 40px; bottom: 34px;
    color: var(--white);
    font-size: 19px;
    font-weight: 500;
  }
  .back-web b { font-weight: 700; }
  /* Front side */
  .card-front {
    left: 470px; top: 470px;
    background: var(--white);
  }
  .brand-front {
    position: absolute;
    left: 30px; top: 118px;
    width: 250px;
    text-align: center;
    color: var(--purple);
    font-size: 34px;
    font-weight: 700;
    line-height: 1.15;
  }
  .brand-front .mark {
    display: block;
    width: 48px; height: 48px;
    margin: 0 auto 14px;
    border-radius: 50%;
    background: var(--purple);
  }
  .divider {
    position: absolute;
    left: 296px; top: 40px;
    width: 2px; height: 280px;
    background: linear-gradient(to bottom, rgba(75,15,107,0), rgba(75,15,107,0.7) 40%, rgba(75,15,107,0.7) 60%, rgba(75,15,107,0));
  }
  .contacts {
    position: absolute;
    left: 320px; top: 40px;
    color: var(--purple-text);
  }
  .person-name { font-size: 20px; font-weight: 700; line-height: 1.1; }
  .person-title { font-size: 12px; color: var(--grey-title); margin-top: 2px; }
  .person-phone { font-size: 14px; margin-bottom: 8px; }
  .address { font-size: 14px; line-height: 1.3; margin-bottom: 4px; }
  .line { font-size: 13px; display: flex; align-items: center; gap: 8px; line-height: 1.45; }
  .line svg { width: 12px; height: 12px; fill: var(--olive); flex: none; }
  .line.web { color: var(--olive); font-weight: 600; }
</style>
</head>
<body>
  <section class="card card-back">
    <div class="brand-emboss"><span class="mark"></span>Hartwell Estates</div>
    <div class="back-web">www.<b>hartwellestates-demo</b>.com</div>
  </section>

  <section class="card card-front">
    <div class="brand-front"><span class="mark"></span>Hartwell Estates</div>
    <div class="divider"></div>
    <div class="contacts">
      <div class="person-name">Dana Pembrook</div>
      <div class="person-title">Broker</div>
      <div class="person-phone">(555).317.6624</div>
      <div class="person-name">Marla Pembrook</div>
      <div class="person-title">Realtor</div>
      <div class="person-phone">(555).609.1385</div>
      <div class="address">418B W. Calloway Ave.<br>Linden Falls, OK. 70913</div>
      <div class="line">
        <svg viewBox="0 0 24 24"><path d="M6.6 10.8a15.1 15.1 0 0 0 6.6 6.6l2.2-2.2c.3-.3.7-.4 1-.2 1.1.4 2.3.6 3.6.6.6 0 1 .4 1 1V20c0 .6-.4 1-1 1C10.6 21 3 13.4 3 4c0-.6.4-1 1-1h3.5c.6 0 1 .4 1 1 0 1.3.2 2.5.6 3.6.1.3 0 .7-.2 1L6.6 10.8z"/></svg>
        (555).240.3918
      </div>
      <div class="line">
        <svg viewBox="0 0 24 24"><path d="M2 5h20v14H2V5zm2 2v.5l8 5 8-5V7H4zm0 2.8V17h16V9.8l-8 5-8-5z"/></svg>
        pembrook@hartwellestates-demo.com
      </div>
      <div class="line web">
        <svg viewBox="0 0 24 24"><path d="M12 2a10 10 0 1 0 0 20 10 10 0 0 0 0-20zm6.9 6h-3a15.6 15.6 0 0 0-1.4-3.6A8 8 0 0 1 18.9 8zM12 4c.8 1.2 1.5 2.5 1.9 4h-3.8c.4-1.5 1.1-2.8 1.9-4zM4.3 14a8 8 0 0 1 0-4h3.4a16 16 0 0 0 0 4H4.3zm.8 2h3a15.6 15.6 0 0 0 1.4 3.6A8 8 0 0 1 5.1 16zm3-8h-3a8 8 0 0 1 4.4-3.6C8.9 5.5 8.4 6.7 8.1 8zM12 20c-.8-1.2-1.5-2.5-1.9-4h3.8c-.4 1.5-1.1 2.8-1.9 4zm2.3-6H9.7a14 14 0 0 1 0-4h4.6a14 14 0 0 1 0 4zm.2 5.6c.6-1.1 1.1-2.3 1.4-3.6h3a8 8 0 0 1-4.4 3.6zm1.8-5.6a16 16 0 0 0 0-4h3.4a8 8 0 0 1 0 4h-3.4z"/></svg>
        www.hartwellestates-demo.com
      </div>
    </div>
  </section>
</body>
</html>
```